Business Card For Halvenmoor Financial Consulting

Hi, I would like a business card designed. Bold, modern.
Please use the same design as the logo. I have also attached the website design to see the overall theme.
Wordmark Font
Color: Hex: #01AEF7

```html
<!DOCTYPE html>
<html lang="en">
<head>
<meta charset="UTF-8">
<title>Halvenmoor Consulting – Business Card</title>
<link rel="stylesheet" href="https://fonts.googleapis.com/css2?family=Sora:wght@600&display=swap">
<style>
  :root {
    --page-bg: #eeeff1;
    --card-top: #467dae;
    --card-mid: #2b5378;
    --card-low: #1d3a55;
    --card-deep: #152a3c;
    --chart-teal: #4a9598;
    --chart-teal-soft: #35707a;
    --accent: #01aef7;
    --wordmark: #ffffff;
  }
  html, body {
    margin: 0;
    width: 1200px;
    height: 1170px;
    overflow: hidden;
    background: var(--page-bg);
  }
  .stage {
    width: 1200px;
    height: 1170px;
    display: flex;
    align-items: center;
    justify-content: center;
  }
  .business-card {
    position: relative;
    width: 1080px;
    height: 617px;
    overflow: hidden;
    background: linear-gradient(180deg, var(--card-top) 0%, var(--card-mid) 30%, var(--card-low) 52%, var(--card-deep) 100%);
    box-shadow: 0 14px 40px rgba(20, 40, 60, 0.25);
  }
  .brand {
    position: absolute;
    top: 218px;
    left: 0;
    right: 0;
    display: flex;
    justify-content: center;
    align-items: flex-start;
    gap: 18px;
    z-index: 2;
  }
  .brand-square {
    width: 68px;
    height: 68px;
    border: 3px solid var(--accent);
    box-sizing: border-box;
    flex: none;
  }
  .brand-name {
    font-family: "Sora", sans-serif;
    font-weight: 600;
    color: var(--wordmark);
    line-height: 1;
  }
  .brand-name .primary {
    display: block;
    font-size: 52px;
    letter-spacing: 1px;
    margin-top: -4px;
  }
  .brand-name .secondary {
    display: block;
    margin-top: 10px;
    font-size: 15px;
    letter-spacing: 21.5px;
  }
  .data-skyline {
    position: absolute;
    left: 0;
    right: 0;
    bottom: 0;
    height: 325px;
    background:
      radial-gradient(circle at 32% 24%, rgba(1, 174, 247, 0.75) 0, rgba(1, 174, 247, 0.2) 1.5%, transparent 6%),
      radial-gradient(circle at 60% 40%, rgba(1, 174, 247, 0.75) 0, rgba(1, 174, 247, 0.2) 1.5%, transparent 6%),
      radial-gradient(circle at 2% 66%, rgba(1, 174, 247, 0.7) 0, rgba(1, 174, 247, 0.2) 1.5%, transparent 5%),
      radial-gradient(circle at 76% 78%, rgba(1, 174, 247, 0.6) 0, transparent 5%),
      radial-gradient(circle at 93% 81%, rgba(1, 174, 247, 0.6) 0, transparent 5%),
      radial-gradient(ellipse at 50% 100%, rgba(74, 149, 152, 0.55) 0%, transparent 70%),
      linear-gradient(180deg, rgba(53, 112, 122, 0) 0%, rgba(53, 112, 122, 0.45) 28%, rgba(74, 149, 152, 0.55) 65%, rgba(53, 112, 122, 0.5) 100%);
  }
</style>
</head>
<body>
  <main class="stage">
    <section class="business-card">
      <div class="brand">
        <div class="brand-square"></div>
        <div class="brand-name">
          <span class="primary">HALVENMOOR</span>
          <span class="secondary">CONSULTING</span>
        </div>
      </div>
      <div class="data-skyline" role="img" aria-label="Decorative illustration of glowing teal bar charts linked by a network of dots and lines"></div>
    </section>
  </main>
</body>
</html>
```